Executive Business Card for Healthcare Company [Need Today]

I need a business card design for a healthcare company. The only branding the company has thus far is a logo. The cards will be utilized by company executives. The design I envision will be vibrant and appealing but with a corporate feel. They shouldn't be too casual or playful. I would like to complete this project TODAY if possible.

Target Market(s)

Healthcare vendors, other executives in healthcare and pharmaceuticals

Industry/Entity Type

Pharmaceutical

Contact Information for Business Card

See attachment

Font styles to use
Serif
Sans Serif

Colors

Designer to choose colors to be used in the design.

```html
<!DOCTYPE html>
<html lang="en">
<head>
<meta charset="utf-8">
<title>Corvane Therapeutics – Business Card</title>
<link rel="stylesheet" href="https://fonts.googleapis.com/css2?family=Arimo:wght@400;700&display=swap">
<style>
  :root {
    --page-bg: #eef1f1;
    --card-white: #ffffff;
    --brand-green: #66c295;
    --brand-teal: #37bdc6;
    --back-teal: #3bbfc8;
    --back-green: #5cc3a2;
    --ink-white: #ffffff;
    --ring-silver: #e4e8ea;
    --card-shadow: 0 10px 28px rgba(0, 0, 0, 0.18);
  }
  * { box-sizing: border-box; margin: 0; padding: 0; }
  html, body {
    width: 1200px;
    height: 900px;
    overflow: hidden;
    background: var(--page-bg);
    font-family: "Arimo", Arial, sans-serif;
  }
  .canvas { position: relative; width: 1200px; height: 900px; }

  .card { position: absolute; box-shadow: var(--card-shadow); overflow: hidden; }

  /* Front */
  .card-front {
    left: 77px; top: 33px; width: 588px; height: 364px;
    background: var(--card-white);
  }
  .card-front .band-art { position: absolute; inset: 0; }
  .brand-lockup {
    position: absolute; left: 121px; top: 48px;
    display: flex; align-items: center; gap: 22px;
  }
  .brand-ring {
    width: 110px; height: 110px; border-radius: 50%;
    border: 4px solid var(--brand-green);
  }
  .brand-name {
    font-size: 34px; font-weight: 400; color: var(--brand-teal);
    line-height: 1.1; letter-spacing: 0.5px;
  }
  .contact-list {
    position: absolute; left: 29px; top: 266px;
    list-style: none; color: var(--ink-white); font-size: 15.5px;
  }
  .contact-list li { display: flex; align-items: center; gap: 4px; height: 21px; }
  .contact-icon { width: 16px; height: 16px; flex: none; }
  .person {
    position: absolute; right: 25px; top: 270px; text-align: right; color: var(--ink-white);
  }
  .person-name { font-size: 19.5px; font-weight: 700; letter-spacing: 0.3px; }
  .person-title { font-size: 15.5px; font-weight: 400; margin-top: 3px; }

  /* Back */
  .card-back {
    left: 388px; top: 505px; width: 567px; height: 352px;
    background: linear-gradient(225deg, var(--back-green) 0%, var(--back-teal) 30%, var(--back-teal) 62%, var(--back-green) 100%);
  }
  .back-ring {
    position: absolute; left: 197px; top: 92px; width: 172px; height: 172px;
    border-radius: 50%; border: 5px solid var(--ring-silver);
    box-shadow: 0 2px 3px rgba(0, 0, 0, 0.18);
  }
</style>
</head>
<body>
<main class="canvas">

  <section class="card card-front" aria-label="Business card front">
    <svg class="band-art" width="588" height="364" viewBox="0 0 588 364" aria-hidden="true">
      <polygon points="0,200 356,200 334,224 0,224" fill="var(--brand-teal)"/>
      <polygon points="0,228 337,228 366,192 588,192 588,364 0,364" fill="var(--brand-green)"/>
    </svg>

    <div class="brand-lockup">
      <div class="brand-ring"></div>
      <div class="brand-name">Corvane<br>Therapeutics</div>
    </div>

    <ul class="contact-list">
      <li>
        <svg class="contact-icon" viewBox="0 0 16 16" aria-hidden="true"><circle cx="8" cy="8" r="7" fill="none" stroke="#fff" stroke-width="1.3"/><path d="M4.5 7.5h7v3h-7z M5.5 7.5c0-2 5-2 5 0" fill="#fff"/></svg>
        555-210-4730
      </li>
      <li>
        <svg class="contact-icon" viewBox="0 0 16 16" aria-hidden="true"><circle cx="8" cy="8" r="7" fill="none" stroke="#fff" stroke-width="1.3"/><rect x="5.8" y="4" width="4.4" height="8" rx="0.8" fill="none" stroke="#fff" stroke-width="1.2"/></svg>
        555-382-6154
      </li>
      <li>
        <svg class="contact-icon" viewBox="0 0 16 16" aria-hidden="true"><circle cx="8" cy="8" r="7" fill="none" stroke="#fff" stroke-width="1.3"/><rect x="4.5" y="5.5" width="7" height="5" fill="#fff"/><path d="M4.5 5.5l3.5 3 3.5-3" fill="none" stroke="var(--brand-green)" stroke-width="0.9"/></svg>
        dhart@corvanerx.com
      </li>
    </ul>

    <div class="person">
      <p class="person-name">DANIEL HART</p>
      <p class="person-title">Senior Director of Marketing</p>
    </div>
  </section>

  <section class="card card-back" aria-label="Business card back">
    <div class="back-ring"></div>
  </section>

</main>
</body>
</html>
```